Government Contracting business needs a website design.

Pellworth & Quine, LLC is a minority owned Service Disabled Veteran Owned Small Business (SDVOSB) that provides Strategic Planning, Public Health Emergency Response, and Data Management Solutions for Federal Civilian and Defense Agencies. We have over 20 years of experience helping health and defense agencies develop concept of operations, deploy assets and personnel in Hot Zones around the world, and deliver goods and services all of the globe.

We are a leader in the field of Data Management. We help our customers develop cloud migration and disaster recovery strategies. We are experts with database management, data replication, queries, consolidation, and records management.

We are looking for a very nice and simple website designs that states clearly what we do as a company and that is easy for our customers to follow. We would like to have some moving pictures that are base on our expertise. We want the website to be easy to use and have the scroll down features that keeps things all on the same page when clicking on the menu. I attached a document with what we need on the website. I will also attach our logo. We want it to look simple clean and very professional.

Target Market(s)

Government Contracting, Management Consulting, Health

Industry/Entity Type

Government

Coding

Coded - Design and coding required

Number of Pages Required

1 page

Font styles to use
Serif

Requirements
Must have
• Very nice picture slides that speaks to our capabilities in Disaster Response, Strategic Planning, and Database Management. Slick look and design. Make sure SDVOSB Logo is right at the beginning of website as our customers is looking for that certification. Very nice colors that blend well with our logo.
Nice to have
• Very nice and slick colors that blends well with logo.
Should not have
• Basic website design that are weary on the eye. No bright colors, just simple colors that looks good with logo.

```html
<!DOCTYPE html>
<html lang="en">
<head>
<meta charset="utf-8">
<title>Pellworth &amp; Quine, LLC</title>
<link href="https://fonts.googleapis.com/css2?family=Playfair+Display:wght@400;700&family=Lora:wght@400;700&display=swap" rel="stylesheet">
<style>
:root{
  --navy:#1f4e6b;
  --navy-dark:#173c54;
  --band:#1e5273;
  --ink:#1c2a36;
  --text:#5b6670;
  --line:#d9dee3;
  --light:#f4f6f8;
  --footer:#1a2028;
  --white:#fff;
}
*{box-sizing:border-box;margin:0;padding:0}
html,body{width:1200px;height:5084px;overflow:hidden}
body{font-family:'Lora',Georgia,serif;color:var(--text);background:var(--white);position:relative}
h1,h2,h3,h4{font-family:'Playfair Display',Georgia,serif;color:var(--ink)}
.section{position:absolute;left:0;width:1200px}
.section-title{text-align:center;font-size:40px;font-weight:700;color:var(--navy);display:flex;align-items:center;justify-content:center;gap:24px}
.section-title::before,.section-title::after{content:"";width:120px;height:1px;background:var(--line)}
.section-lead{text-align:center;font-size:15px;line-height:26px;width:620px;margin:14px auto 0}
.btn{display:inline-block;background:var(--navy);color:var(--white);font-size:15px;letter-spacing:1px;padding:18px 34px;border-radius:3px}

/* top bar */
.topbar{top:0;height:32px;background:var(--navy-dark);color:#dfe8ef;font-size:13px;display:flex;align-items:center;justify-content:space-between;padding:0 80px}
.topbar-right{display:flex;align-items:center;gap:16px}
.dot{width:20px;height:20px;border-radius:50%;background:#3a6a89;display:inline-block}

/* nav */
.nav{top:32px;height:118px;display:flex;align-items:center;justify-content:space-between;padding:0 70px;border-bottom:1px solid var(--line)}
.brand{display:flex;align-items:center;gap:14px;font-size:24px;font-weight:700;color:var(--navy)}
.brand-mark{width:34px;height:34px;background:var(--navy)}
.nav-links{display:flex;gap:26px;font-size:15px;color:var(--ink)}
.nav-links .active{color:var(--navy);font-weight:700;border-bottom:2px solid var(--navy);padding-bottom:4px}

/* hero */
.hero{top:150px;height:580px;background:linear-gradient(90deg,#1f4e6b 0%,#2b6283 38%,#8ca3b2 62%,#c9d3da 100%)}
.hero-text{position:absolute;left:70px;top:130px;width:470px;font-family:'Playfair Display',Georgia,serif;font-size:36px;line-height:52px;font-weight:700;color:var(--white)}

/* about */
.about{top:730px;height:406px;padding-top:80px;text-align:center}
.about .section-lead{width:720px;margin-bottom:40px}

/* why */
.why{top:1136px;height:544px;display:flex}
.why-photo{width:570px;height:544px;background:linear-gradient(135deg,#dfe3e7,#b7bec5 60%,#8c949c)}
.why-panel{flex:1;background:var(--navy);padding:60px 90px 0 60px;color:#dbe6ee}
.why-panel h2{color:var(--white);font-size:40px;margin-bottom:20px}
.why-panel p{font-size:14px;line-height:24px;margin-bottom:26px}
.why-list{list-style:none}
.why-list li{display:flex;gap:14px;font-size:14px;line-height:23px;margin-bottom:22px;color:var(--white);font-weight:700}
.why-list svg{flex:none;margin-top:3px}

/* capabilities */
.caps{top:1680px;height:570px;padding-top:70px}
.cap-grid{display:flex;gap:24px;justify-content:center;margin-top:40px}
.cap-card{width:246px;height:240px;position:relative;background:linear-gradient(160deg,#c8d0d7,#7f8f9d)}
.cap-card .cap-name{position:absolute;left:0;right:0;bottom:0;height:76px;background:linear-gradient(transparent,rgba(16,40,58,.9));color:var(--white);font-family:'Playfair Display',Georgia,serif;font-weight:700;font-size:17px;padding:30px 60px 0 16px;line-height:21px}
.play{position:absolute;right:14px;bottom:22px;width:30px;height:30px;border-radius:50%;background:var(--white);display:flex;align-items:center;justify-content:center}

/* agencies */
.agencies{top:2250px;height:550px;background:linear-gradient(180deg,#262c33,#1c2127);padding-top:66px}
.agencies .section-title{color:var(--white)}
.agencies .section-lead{color:#c9d0d6}
.arrows{display:flex;justify-content:center;gap:8px;margin-top:22px}
.arrows span{width:36px;height:36px;background:var(--white);display:flex;align-items:center;justify-content:center}
.agency-row{display:flex;justify-content:center;gap:56px;margin-top:50px}
.agency{width:130px;text-align:center;color:var(--white);font-family:'Playfair Display',Georgia,serif;font-weight:700;font-size:15px;line-height:20px}
.agency-icon{width:122px;height:122px;background:var(--white);margin:0 auto 20px;display:flex;align-items:center;justify-content:center;border-radius:4px}

/* partners */
.partners{top:2800px;height:400px;padding-top:76px}
.partner-row{display:flex;justify-content:center;gap:40px;margin-top:40px}
.partner{width:220px;height:90px;border:1px solid var(--line);display:flex;align-items:center;justify-content:center;font-family:'Playfair Display',Georgia,serif;font-weight:700;font-size:20px;color:var(--navy)}

/* leadership */
.leaders{top:3200px;height:520px;background:var(--band);padding-top:60px}
.leaders .section-title{color:var(--white)}
.leaders .section-title::before,.leaders .section-title::after{background:#4e7b98}
.leader-row{display:flex;justify-content:center;gap:40px;margin-top:50px}
.leader-card{width:480px;height:300px;background:var(--white);border-radius:6px;padding:30px 36px}
.leader-head{display:flex;align-items:center;gap:20px;margin-bottom:22px}
.avatar{width:84px;height:84px;border-radius:50%;background:linear-gradient(160deg,#c5ccd2,#8a949d);flex:none}
.leader-head h3{font-size:20px}
.leader-head span{font-size:13px;color:var(--navy)}
.leader-card p{font-size:13px;line-height:22px}
.leader-card .more{display:block;margin-top:16px;font-size:12px;font-weight:700;color:var(--navy);text-decoration:underline}

/* blog */
.blog{top:3720px;height:580px;padding-top:50px}
.blog-row{display:flex;justify-content:center;gap:30px;margin-top:40px}
.post{width:346px;height:390px;box-shadow:0 2px 10px rgba(0,0,0,.12);position:relative}
.post-photo{height:180px;background:linear-gradient(150deg,#d9dde1,#9ca6af)}
.post h4{font-size:18px;line-height:24px;padding:16px 20px 8px}
.post p{font-size:13px;line-height:21px;padding:0 20px}
.post-bar{position:absolute;left:0;right:0;bottom:0;height:44px;background:var(--navy);color:var(--white);font-size:12px;display:flex;align-items:center;gap:26px;padding:0 20px}
.post-bar .go{margin-left:auto}

/* footer */
.footer{top:4300px;height:720px;background:linear-gradient(180deg,#1f262e,#161b21)}
.footer-info{position:absolute;left:70px;top:150px;width:380px;color:#c9d0d6;font-size:14px;line-height:24px}
.footer-brand{display:flex;align-items:center;gap:14px;font-family:'Lora',Georgia,serif;font-weight:700;font-size:26px;color:var(--white);margin-bottom:28px}
.footer-brand .brand-mark{background:var(--white)}
.footer-contact{margin-top:30px;display:flex;flex-direction:column;gap:16px}
.footer-contact div{display:flex;align-items:center;gap:12px}
.contact-box{position:absolute;left:652px;top:-52px;width:470px;height:660px;background:var(--light);box-shadow:0 4px 18px rgba(0,0,0,.25);padding:44px 48px}
.contact-box h2{text-align:center;font-size:34px;color:var(--navy);margin-bottom:28px}
.field{height:44px;background:var(--white);border:1px solid var(--line);margin-bottom:16px;font-size:13px;color:#8a949d;padding:12px 14px;display:flex;justify-content:space-between}
.field.message{height:120px}
.submit{display:block;width:170px;margin:10px auto 0;text-align:center;background:var(--navy);color:var(--white);font-size:14px;letter-spacing:1px;padding:14px 0}

/* bottom bar */
.bottombar{top:5020px;height:64px;background:var(--navy-dark);color:#c9d4dc;font-size:13px;display:flex;align-items:center;justify-content:space-between;padding:0 70px}
.bottombar .topbar-right .dot{width:24px;height:24px}
</style>
</head>
<body>

<div class="section topbar">
  <span>Welcome to Pellworth &amp; Quine, LLC</span>
  <div class="topbar-right">
    <span>&#9742; 202-555-0148</span>
    <span class="dot"></span><span class="dot"></span><span class="dot"></span>
  </div>
</div>

<header class="section nav">
  <div class="brand"><span class="brand-mark"></span>Pellworth &amp; Quine</div>
  <nav class="nav-links">
    <span class="active">Home</span><span>About</span><span>Why Choose Us?</span><span>Core Capabilities</span><span>Services</span><span>Team</span><span>Join Us</span><span>Contact</span>
  </nav>
</header>

<section class="section hero" role="img" aria-label="Team meeting around a laptop in a bright office">
  <p class="hero-text">We are a Service Disabled Veteran Owned Small Business (SDVOSB) specializing in Mission Oriented Health IT for the Defense and VA Community.</p>
</section>

<section class="section about">
  <h2 class="section-title">About Pellworth &amp; Quine LLC</h2>
  <p class="section-lead">Pellworth &amp; Quine LLC is a minority owned Service Disabled Veteran Owned Small Business (SDVOSB) that provides Strategic Planning, Public Health Emergency Response, and Data Management Solutions for Federal Civilian and Defense Agencies. We have over 20 years of experience helping health and defense agencies deploy assets and personnel in Hot Zones around the world.</p>
  <span class="btn">READ MORE</span>
</section>

<section class="section why">
  <div class="why-photo" role="img" aria-label="Three smiling business professionals standing together"></div>
  <div class="why-panel">
    <h2>Why Choose Us?</h2>
    <p>Our team brings decades of field and federal experience to every engagement. We plan carefully, respond quickly and deliver results that agencies can rely on.</p>
    <ul class="why-list">
      <li><svg width="16" height="16" viewBox="0 0 16 16"><rect x="0.5" y="0.5" width="15" height="15" fill="none" stroke="#fff"/><path d="M4 8l3 3 5-6" fill="none" stroke="#fff" stroke-width="1.6"/></svg>Over 20 years of experience deploying assets and personnel to disaster zones around the US and the world.</li>
      <li><svg width="16" height="16" viewBox="0 0 16 16"><rect x="0.5" y="0.5" width="15" height="15" fill="none" stroke="#fff"/><path d="M4 8l3 3 5-6" fill="none" stroke="#fff" stroke-width="1.6"/></svg>Over 20 years of experience developing concept of operations and stakeholder management strategies for Federal Agencies.</li>
      <li><svg width="16" height="16" viewBox="0 0 16 16"><rect x="0.5" y="0.5" width="15" height="15" fill="none" stroke="#fff"/><path d="M4 8l3 3 5-6" fill="none" stroke="#fff" stroke-width="1.6"/></svg>Over 18 years of experience with database management and replication.</li>
      <li><svg width="16" height="16" viewBox="0 0 16 16"><rect x="0.5" y="0.5" width="15" height="15" fill="none" stroke="#fff"/><path d="M4 8l3 3 5-6" fill="none" stroke="#fff" stroke-width="1.6"/></svg>Highly educated consultants with over 80% possessing advance degrees and industry certifications.</li>
    </ul>
  </div>
</section>

<section class="section caps">
  <h2 class="section-title">Core Capabilities</h2>
  <p class="section-lead">We combine planning, rapid response and data expertise to support the missions of health and defense agencies nationwide.</p>
  <div class="cap-grid">
    <div class="cap-card" role="img" aria-label="Planning session with charts on a desk"><div class="cap-name">Strategic Planning</div><span class="play"><svg width="10" height="12" viewBox="0 0 10 12"><path d="M0 0l10 6-10 6z" fill="#1f4e6b"/></svg></span></div>
    <div class="cap-card" role="img" aria-label="Medical response staff at work"><div class="cap-name">Public Health Emergency Response</div><span class="play"><svg width="10" height="12" viewBox="0 0 10 12"><path d="M0 0l10 6-10 6z" fill="#1f4e6b"/></svg></span></div>
    <div class="cap-card" role="img" aria-label="Analyst working with data on screens"><div class="cap-name">Data Management Services</div><span class="play"><svg width="10" height="12" viewBox="0 0 10 12"><path d="M0 0l10 6-10 6z" fill="#1f4e6b"/></svg></span></div>
    <div class="cap-card" role="img" aria-label="Contract meeting in an office"><div class="cap-name">Contracts Vehicles</div><span class="play"><svg width="10" height="12" viewBox="0 0 10 12"><path d="M0 0l10 6-10 6z" fill="#1f4e6b"/></svg></span></div>
  </div>
</section>

<section class="section agencies" role="img" aria-label="Dark backdrop of a medical monitor display">
  <h2 class="section-title">Agencies We Serve</h2>
  <p class="section-lead">We partner with federal health and defense agencies to plan, respond and manage the data behind their missions.</p>
  <div class="arrows">
    <span><svg width="10" height="14" viewBox="0 0 10 14"><path d="M8 1L2 7l6 6" fill="none" stroke="#1c2a36" stroke-width="2"/></svg></span>
    <span><svg width="10" height="14" viewBox="0 0 10 14"><path d="M2 1l6 6-6 6" fill="none" stroke="#1c2a36" stroke-width="2"/></svg></span>
  </div>
  <div class="agency-row">
    <div class="agency"><div class="agency-icon"><svg width="50" height="50" viewBox="0 0 50 50"><path d="M18 4h14v14h14v14H32v14H18V32H4V18h14z" fill="#1f4e6b"/></svg></div>Office of Disease Readiness</div>
    <div class="agency"><div class="agency-icon"><svg width="56" height="50" viewBox="0 0 56 50"><circle cx="28" cy="25" r="21" fill="none" stroke="#1f4e6b" stroke-width="5"/><path d="M18 25l7 7 13-14" fill="none" stroke="#1f4e6b" stroke-width="5"/></svg></div>Bureau of Food Safety</div>
    <div class="agency"><div class="agency-icon"><svg width="56" height="50" viewBox="0 0 56 50"><path d="M4 16L28 4l24 12z" fill="#1f4e6b"/><rect x="8" y="20" width="6" height="20" fill="#1f4e6b"/><rect x="20" y="20" width="6" height="20" fill="#1f4e6b"/><rect x="31" y="20" width="6" height="20" fill="#1f4e6b"/><rect x="42" y="20" width="6" height="20" fill="#1f4e6b"/><rect x="4" y="43" width="48" height="5" fill="#1f4e6b"/></svg></div>Institute of Health Research</div>
    <div class="agency"><div class="agency-icon"><svg width="52" height="48" viewBox="0 0 52 48"><path d="M26 46C10 34 2 24 2 14A12 12 0 0 1 26 9a12 12 0 0 1 24 5c0 10-8 20-24 32z" fill="#1f4e6b"/><path d="M10 22h10l3-6 5 12 3-6h11" fill="none" stroke="#fff" stroke-width="3"/></svg></div>Military Health Office</div>
    <div class="agency"><div class="agency-icon"><svg width="52" height="52" viewBox="0 0 52 52"><path d="M24 2h4l2 18 20 10v5l-20-5-1 12 6 5v3l-9-2-9 2v-3l6-5-1-12-20 5v-5l20-10z" fill="#1f4e6b"/></svg></div>Civil Aviation Office</div>
  </div>
</section>

<section class="section partners">
  <h2 class="section-title">Our Partners</h2>
  <p class="section-lead">We team with respected firms across consulting, aerospace and technology to deliver complete solutions.</p>
  <div class="partner-row">
    <div class="partner">Aldercrest Advisory</div>
    <div class="partner">Westbury Aerospace</div>
    <div class="partner">Kestrel Partners</div>
    <div class="partner">Harlan Systems</div>
  </div>
</section>

<section class="section leaders">
  <h2 class="section-title">Leadership Team</h2>
  <div class="leader-row">
    <div class="leader-card">
      <div class="leader-head"><div class="avatar" role="img" aria-label="Portrait of the president"></div><div><h3>Ret. SFC Marcus T. Pellworth</h3><span>President &amp; CEO</span></div></div>
      <p>Retired Army Sergeant First Class Mr. Pellworth is the founder and CEO of Pellworth &amp; Quine LLC. He retired from the US Army after over 20 years of service which included tours in Operation Desert Storm.</p>
      <span class="more">READ MORE</span>
    </div>
    <div class="leader-card">
      <div class="leader-head"><div class="avatar" role="img" aria-label="Portrait of the business development manager"></div><div><h3>Mr. Daniel K. Quine</h3><span>Business Development Manager</span></div></div>
      <p>Mr. Quine brings over 10 years of business development experience to Pellworth &amp; Quine LLC. Prior to joining, he led business development capture for large and midsize defense companies in the Washington DC area.</p>
      <span class="more">READ MORE</span>
    </div>
  </div>
</section>

<section class="section blog">
  <h2 class="section-title">Recent Blog</h2>
  <div class="blog-row">
    <article class="post"><div class="post-photo" role="img" aria-label="Family smiling together at home"></div><h4>Lorem Ipsum dummy printing and typesetting industry.</h4><p>Lorem Ipsum is simply dummy text of the printing and typesetting industry. Lorem Ipsum has been the standard dummy text.</p><div class="post-bar"><span>&#128197; 23 April 2018</span><span>&#128172; Comment</span><span class="go">&#8594;</span></div></article>
    <article class="post"><div class="post-photo" role="img" aria-label="Professional reviewing documents at a desk"></div><h4>Lorem Ipsum dummy printing and Printing Text typesetting industry.</h4><p>Lorem Ipsum is simply dummy text of the printing and typesetting industry. Lorem Ipsum has been the standard dummy text.</p><div class="post-bar"><span>&#128197; 23 April 2018</span><span>&#128172; Comment</span><span class="go">&#8594;</span></div></article>
    <article class="post"><div class="post-photo" role="img" aria-label="Colleagues in a business meeting"></div><h4>Lorem Ipsum dummy printing and typesetting industry.</h4><p>Lorem Ipsum is simply dummy text of the printing and typesetting industry. Lorem Ipsum has been the standard dummy text.</p><div class="post-bar"><span>&#128197; 23 April 2018</span><span>&#128172; Comment</span><span class="go">&#8594;</span></div></article>
  </div>
</section>

<footer class="section footer" role="img" aria-label="Dark city skyline backdrop">
  <div class="footer-info">
    <div class="footer-brand"><span class="brand-mark"></span>Pellworth &amp; Quine</div>
    <p>Pellworth &amp; Quine LLC was created by Retired Army veterans seeking to provide mission oriented Health IT support to the Department of Defense and Veterans Affairs community.</p>
    <div class="footer-contact">
      <div><svg width="14" height="18" viewBox="0 0 14 18"><path d="M7 0a7 7 0 0 1 7 7c0 5-7 11-7 11S0 12 0 7a7 7 0 0 1 7-7z" fill="#c9d0d6"/><circle cx="7" cy="7" r="2.5" fill="#1f262e"/></svg>1870 Linden Crest Dr, Atlanta, GA</div>
      <div><svg width="16" height="16" viewBox="0 0 16 16"><path d="M3 1l3 3-2 2a9 9 0 0 0 6 6l2-2 3 3-2 2C7 15 1 9 1 3z" fill="#c9d0d6"/></svg>202-555-0148 &nbsp;&nbsp;&nbsp; &#9993; info@pellworthquine.com</div>
    </div>
  </div>
  <div class="contact-box">
    <h2>Get In Touch</h2>
    <div class="field">Name *</div>
    <div class="field">Email *</div>
    <div class="field">Phone *</div>
    <div class="field">Select Category * <span>&#9662;</span></div>
    <div class="field message">Message</div>
    <span class="submit">SUBMIT</span>
  </div>
</footer>

<div class="section bottombar">
  <span>&copy; 2018 by Pellworth &amp; Quine LLC All Right Reserved.</span>
  <div class="topbar-right"><span class="dot"></span><span class="dot"></span><span class="dot"></span></div>
</div>

</body>
</html>
```